Velvet Meadow Hamper company needs a brochure design

We need a brochure design for a new company in Dubai called 'Velvet Meadow Hampers'. We already have a logo designed which I have attached and would like to use this and the green/gold/white colours for our brochure. Our company initially will be supplying Velvet Meadow Hamper wear of traditional wicker baskets in many designs which hold all the cutlery, crockery and accessories. We will also be selling picnic accessories. We want to purvey a sense of luxury and class in line with our logo. I have attached some photos of the picnicwear. As our products are changing all the time I thought a fold out cover which stays the same and then product cards inserted into the folder which can be changed according to our product changes. I am looking for a fairly simple design and each product card should have at least one photo of the product on it with a spec and description also. On the cover of the folder I would like room to write about the company and what we do, this can be inside or out and may or may not include photos. I have the logo designs in illustrator format and pdf. Please contact if any more information is needed.
Updates

Reason: I have extended this deadline as there are some content changes taking place.

Industry/Entity Type

It Company

```html
<!DOCTYPE html>
<html lang="en">
<head>
<meta charset="utf-8">
<title>Velvet Meadow Hampers – Cream Cooler Bag Product Card</title>
<link rel="stylesheet" href="https://fonts.googleapis.com/css2?family=Montserrat:wght@700&family=Gelasio:wght@400&display=swap">
<style>
  :root {
    --forest: #1b331d;
    --gold: #c9a53a;
    --gold-soft: #a88a3a;
    --paper: #ffffff;
    --text-light: #f1efe6;
    --band-dark: #6b2a1a;
    --band-mid: #c08a3a;
    --band-light: #fbf4dc;
  }
  * { margin: 0; padding: 0; box-sizing: border-box; }
  html, body {
    width: 1200px; height: 1000px; overflow: hidden;
    background: var(--paper);
  }
  .canvas { position: relative; width: 1200px; height: 1000px; }

  .card {
    position: absolute; top: 150px; width: 493px; height: 700px;
    background: var(--forest); overflow: hidden;
  }
  .card--front { left: 100px; }
  .card--back { left: 607px; }

  .gold-band {
    position: absolute; left: 0; width: 100%; height: 7px;
    background: linear-gradient(90deg, var(--band-dark) 0%, var(--band-mid) 35%, var(--band-light) 60%, var(--band-mid) 80%, var(--band-dark) 100%);
  }
  .gold-band--top { top: 147px; height: 6px; }
  .gold-band--bottom { top: 513px; }

  .brand {
    position: absolute; top: 64px; left: 0; width: 100%;
    text-align: center;
    font-family: "Montserrat", sans-serif; font-weight: 700;
    font-size: 11.5px; letter-spacing: 2.4px; text-transform: uppercase;
    color: var(--gold);
  }
  .brand__dot {
    display: block; width: 8px; height: 8px; border-radius: 50%;
    background: var(--gold); margin: 0 auto 6px;
  }

  .product-photo {
    position: absolute; top: 153px; left: 0; width: 100%; height: 360px;
    background: var(--paper);
  }
  .product-photo__area {
    position: absolute; left: 72px; top: 32px; width: 330px; height: 290px;
    background: radial-gradient(ellipse at 50% 55%, #c9cdd2 0%, #b3b8be 55%, #e8eaec 85%, #ffffff 100%);
    border-radius: 12px;
  }

  .title {
    font-family: "Montserrat", sans-serif; font-weight: 700;
    color: var(--gold); text-transform: uppercase;
  }
  .card--front .title {
    position: absolute; left: 28px; top: 535px;
    font-size: 23px; letter-spacing: 3.2px;
  }
  .description {
    position: absolute; left: 28px; top: 571px; width: 380px;
    font-family: "Gelasio", serif; font-size: 11.3px; line-height: 13px;
    color: var(--text-light);
  }
  .faint-flourish {
    position: absolute; right: 0; top: 585px; width: 40px; height: 80px;
    background: #28412a; border-radius: 20px 0 0 20px;
  }
  .web {
    position: absolute; left: 0; bottom: 14px; width: 100%;
    text-align: center;
    font-family: "Gelasio", serif; font-size: 10.5px; color: var(--gold);
  }

  .overview {
    position: absolute; left: 0; top: 228px; width: 100%;
  }
  .rule { display: block; width: 133px; height: 1px; background: var(--gold-soft); margin: 0 auto; }
  .ornament { display: block; width: 56px; height: 14px; margin: 0 auto; background: #6f6a33; border-radius: 7px; }
  .ornament--top { margin-bottom: 8px; }
  .ornament--bottom { margin-top: 4px; }
  .card--back .title {
    text-align: center; font-size: 21px; letter-spacing: 3.6px; margin-top: 23px; line-height: 26px;
  }
  .subtitle {
    text-align: center; font-family: "Gelasio", serif; font-size: 15px;
    letter-spacing: 1px; color: var(--gold); line-height: 18px;
  }
  .spec-list {
    list-style: none; margin: 17px 0 8px 98px; width: 300px;
    font-family: "Gelasio", serif; font-size: 10.8px; line-height: 16.6px;
    color: var(--text-light);
  }
  .spec-list li { position: relative; padding-left: 17px; }
  .spec-list li::before {
    content: ""; position: absolute; left: 2px; top: 6px;
    width: 6px; height: 5px; background: var(--gold);
  }
</style>
</head>
<body>
<main class="canvas">
  <section class="card card--front">
    <div class="brand"><span class="brand__dot"></span>Velvet Meadow Hampers</div>
    <div class="gold-band gold-band--top"></div>
    <div class="product-photo">
      <div class="product-photo__area" role="img" aria-label="Photo of the cream insulated cooler bag with top carry handle and zip closure"></div>
    </div>
    <div class="gold-band gold-band--bottom"></div>
    <h1 class="title">Cream Cooler Bag</h1>
    <p class="description">A stylish cream cooler bag to keep your perishable food and drinks cool.<br>An ideal accessory for all your picnic needs.</p>
    <div class="faint-flourish" role="img" aria-label="Faint decorative flourish"></div>
    <p class="web">www.velvetmeadowhampers.com</p>
  </section>

  <section class="card card--back">
    <div class="overview">
      <span class="ornament ornament--top" role="img" aria-label="Gold ornamental flourish"></span>
      <span class="rule"></span>
      <h2 class="title">Cream Cooler Bag</h2>
      <p class="subtitle">OVERVIEW</p>
      <ul class="spec-list">
        <li>Coordinated Cream Colouring with Velvet Meadow Hampers basket range</li>
        <li>Features a water resistant exterior and insulated lining for maximum insulation</li>
        <li>Measurements, 260 x 170 x 160mm</li>
        <li>Made from Polyester</li>
      </ul>
      <span class="rule"></span>
      <span class="ornament ornament--bottom" role="img" aria-label="Gold ornamental flourish"></span>
    </div>
    <p class="web">www.velvetmeadowhampers.com</p>
  </section>
</main>
</body>
</html>
```